A website for Kovadrel Limited

We need a new and modern website for our company. We are engineering consultants and contractors (EPC) in the oil and gas industry and building services industry.
What we do:
Engineering, procurement, construction
Automation (safety and process)
Non-destructive testing
Training
We have an existing website and the content can be referred from there since we are remaking the website
For more information visit Kovadrel Limited Kenya

```html
<!DOCTYPE html>
<html lang="en">
<head>
<meta charset="utf-8">
<title>Kovadrel Limited — Engineering Consultants and Contractors</title>
<link rel="stylesheet" href="https://fonts.googleapis.com/css2?family=Cinzel:wght@600;700;800&family=Montserrat:ital,wght@0,400;0,500;0,600;0,700;1,400&display=swap">
<style>
:root{
  --orange:#ec7a2d;
  --orange-light:#f6ad62;
  --orange-deep:#d9611b;
  --ink:#1c1c1c;
  --text:#4a4a4a;
  --muted:#8a8a8a;
  --grey-bg:#efeeee;
  --white:#ffffff;
  --dark:#2a2829;
}
*{box-sizing:border-box;margin:0;padding:0}
html,body{width:1200px;height:5314px;overflow:hidden}
body{position:relative;background:var(--white);font-family:"Montserrat",sans-serif;color:var(--text)}
.abs{position:absolute}
.heading{font-family:"Cinzel",serif;font-weight:800;color:var(--ink);text-align:center;letter-spacing:1px}
.heading-rule{position:absolute;left:550px;width:100px;height:5px;background:var(--orange)}

/* header */
.site-header{position:absolute;left:0;top:0;width:1200px;height:103px;background:var(--white)}
.brand{position:absolute;left:150px;top:18px;display:flex;align-items:center;gap:8px}
.brand-dot{width:70px;height:70px;border-radius:50%;background:var(--orange)}
.brand-name{font-family:"Montserrat",sans-serif;font-weight:500;font-size:22px;line-height:29px;color:var(--orange-deep);text-transform:uppercase}
.contact-chip{position:absolute;top:36px;display:flex;align-items:center;gap:10px}
.chip-icon{width:36px;height:36px;border-radius:50%;background:var(--orange);display:flex;align-items:center;justify-content:center}
.chip-text{font-size:12.5px;line-height:17px;color:#555;font-weight:500}
.cart{position:absolute;left:1008px;top:35px;width:38px;height:38px;border-radius:50%;background:var(--orange);display:flex;align-items:center;justify-content:center}

.main-nav{position:absolute;left:0;top:103px;width:1200px;height:56px;background:linear-gradient(90deg,var(--orange) 0%,var(--orange-light) 100%)}
.main-nav ul{list-style:none;position:relative;height:56px}
.main-nav li{position:absolute;top:21px;font-size:13px;font-weight:600;color:var(--white);letter-spacing:.3px}

/* hero */
.hero{position:absolute;left:0;top:159px;width:1200px;height:651px;overflow:hidden}
.hero-photo{position:absolute;inset:0;background:
  radial-gradient(ellipse at 55% 40%,rgba(240,150,90,.65) 0%,rgba(170,95,80,.35) 35%,rgba(0,0,0,0) 65%),
  linear-gradient(180deg,#3e4457 0%,#7a6070 30%,#b27560 50%,#3a3436 72%,#18181b 100%)}
.hero-title{position:absolute;left:0;top:192px;width:1200px;text-align:center;font-family:"Cinzel",serif;font-weight:800;font-size:54px;color:var(--white);letter-spacing:2px}
.hero-sub{position:absolute;left:0;top:270px;width:1200px;text-align:center;font-family:"Cinzel",serif;font-weight:600;font-size:19px;color:var(--white);letter-spacing:1px}
.btn{position:absolute;background:var(--orange);color:var(--white);font-size:13px;font-weight:700;text-transform:uppercase;display:flex;align-items:center;justify-content:center}
.btn-framed::after{content:"";position:absolute;left:6px;top:6px;right:-6px;bottom:-6px;border:2px solid var(--orange);pointer-events:none}
.hero-curve{position:absolute;left:0;bottom:0;width:1200px;height:80px}

/* about */
.about-photo-ring{position:absolute;left:112px;top:916px;width:448px;height:436px;border-radius:50%;border:3px solid #b3401f}
.about-photo{position:absolute;left:128px;top:930px;width:416px;height:410px;border-radius:50%;background:radial-gradient(circle at 75% 50%,#f4c59a 0%,#c58669 30%,#6e6d80 60%,#3e3f50 100%)}
.about-copy{position:absolute;left:598px;top:948px;width:440px}
.about-copy h2{font-family:"Cinzel",serif;font-weight:800;font-size:45px;color:var(--ink);letter-spacing:1px}
.about-rule{width:104px;height:5px;background:var(--orange);margin-top:6px}
.about-copy p{font-size:13.4px;line-height:23.5px;color:#444;margin-top:24px}
.about-copy p + p{margin-top:22px}

/* services */
.services{position:absolute;left:0;top:1480px;width:1200px;height:576px;background:linear-gradient(180deg,#f1f0f0 0%,#ebeaea 60%,#f4f4f4 100%)}
.service-card{position:absolute;top:207px;height:220px;border-radius:34px/70px;background:linear-gradient(180deg,#f09b55 0%,var(--orange) 100%);color:var(--white);text-align:center}
.service-icon{width:68px;height:68px;margin:26px auto 0;border-radius:8px;background:rgba(255,255,255,.25)}
.service-name{font-size:11.5px;font-weight:500;line-height:16px;margin-top:22px;text-transform:uppercase;height:34px;display:flex;align-items:center;justify-content:center}
.service-link{font-family:"Cinzel",serif;font-size:11px;font-weight:600;text-decoration:underline;margin-top:16px;color:#fde4cf}

/* products */
.products{position:absolute;left:0;top:2056px;width:1200px;height:662px;background:radial-gradient(ellipse at 50% 40%,#6e6a6c 0%,#3c3a3c 45%,#1f1d1e 100%)}
.product-card{position:absolute;top:206px;width:214px;height:285px;background:var(--white)}
.product-card.active{outline:3px solid var(--orange);outline-offset:-1px}
.product-photo{width:214px;height:221px}
.product-label{height:64px;display:flex;align-items:center;justify-content:center;font-size:17px;font-weight:700;color:var(--ink);letter-spacing:.3px}

/* projects */
.project-card{position:absolute;top:2891px;width:293px;height:371px;background:var(--white);box-shadow:0 3px 14px rgba(0,0,0,.12)}
.project-photo{width:293px;height:202px}
.project-body{padding:26px 28px 0}
.project-title{font-size:13.5px;font-weight:700;color:var(--ink);line-height:18px;text-transform:uppercase;min-height:38px}
.project-text{font-size:11.5px;line-height:14px;color:var(--muted);margin-top:10px}
.project-link{font-size:11.5px;font-weight:600;color:var(--orange);margin-top:3px}

/* clients */
.clients-bg{position:absolute;left:0;top:3378px;width:1200px;height:560px}
.quote{position:absolute;left:150px;top:3632px;width:900px;text-align:center;font-style:italic;font-size:19px;line-height:29px;color:#444}
.client-avatar{position:absolute;left:478px;top:3744px;width:100px;height:100px;border-radius:50%;background:radial-gradient(circle at 50% 40%,#e2b27a 0%,#7f8a5c 60%,#4b5b3a 100%)}
.client-name{position:absolute;left:594px;top:3768px;font-size:17px;font-weight:600;color:var(--ink)}
.client-role{position:absolute;left:594px;top:3794px;font-size:13px;color:#444}

/* partners */
.partner-badge{position:absolute;top:4158px;width:96px;height:96px;border-radius:50%;background:#9a9a9a}

/* quote form */
.quote-section{position:absolute;left:0;top:4341px;width:1200px;height:443px;background:linear-gradient(180deg,#f39a50 0%,var(--orange) 100%)}
.field{position:absolute;background:var(--white);font-size:12.5px;color:#666;padding:13px 14px}
.submit{position:absolute;left:542px;top:4666px;width:116px;height:40px;background:#1d1d1d;color:var(--white);font-size:14px;font-weight:700;display:flex;align-items:center;justify-content:center;text-transform:uppercase}

/* footer */
.site-footer{position:absolute;left:0;top:4784px;width:1200px;height:530px;background:var(--white)}
.footer-skyline{position:absolute;left:0;bottom:0;width:1200px;height:170px;background:linear-gradient(180deg,rgba(246,173,98,0) 0%,rgba(246,173,98,.45) 40%,rgba(236,122,45,.75) 100%)}
.footer-divider{position:absolute;top:4852px;width:2px;height:250px;background:#d9d9d9}
.footer-heading{position:absolute;top:4876px;font-size:15px;font-weight:700;color:var(--ink);text-transform:uppercase}
.footer-rule{position:absolute;top:4905px;width:32px;height:3px;background:#d0d0d0}
.footer-rule::before{content:"";position:absolute;left:0;top:0;width:11px;height:3px;background:var(--orange)}
.footer-menu{position:absolute;left:528px;top:4940px;list-style:none}
.footer-menu li{font-size:12.5px;line-height:25px;color:#444}
.contact-row{position:absolute;left:738px;display:flex;gap:16px;align-items:flex-start}
.contact-row .chip-icon{flex:0 0 36px}
.contact-row span{font-size:12.5px;line-height:22px;color:#444}
.social{position:absolute;top:5054px;width:26px;height:26px;border-radius:50%;background:var(--orange)}
.copyright{position:absolute;left:0;top:5244px;width:1200px;text-align:center;font-size:13.5px;color:var(--ink);font-weight:500}
</style>
</head>
<body>

<header class="site-header">
  <div class="brand">
    <div class="brand-dot"></div>
    <div class="brand-name">Kovadrel<br>Limited</div>
  </div>
  <div class="contact-chip" style="left:528px">
    <div class="chip-icon"><svg width="16" height="12" viewBox="0 0 16 12"><rect x="0.5" y="0.5" width="15" height="11" rx="1.5" fill="none" stroke="#fff"/><path d="M1 1l7 6 7-6" fill="none" stroke="#fff"/></svg></div>
    <div class="chip-text">EMAIL US:<br>INFO@KOVADREL.CO.KE</div>
  </div>
  <div class="contact-chip" style="left:772px">
    <div class="chip-icon"><svg width="16" height="16" viewBox="0 0 24 24"><path fill="#fff" d="M6.6 10.8a15.1 15.1 0 006.6 6.6l2.2-2.2c.3-.3.7-.4 1-.2 1.1.4 2.3.6 3.6.6.6 0 1 .4 1 1V20c0 .6-.4 1-1 1A17 17 0 013 4c0-.6.4-1 1-1h3.5c.6 0 1 .4 1 1 0 1.3.2 2.5.6 3.6.1.3 0 .7-.2 1z"/></svg></div>
    <div class="chip-text">+254 700 555 014<br>+254 700 555 027</div>
  </div>
  <div class="cart"><svg width="16" height="16" viewBox="0 0 16 16"><path d="M3 6h10l-1 8H4z" fill="#fff"/><path d="M5.5 6V4.5a2.5 2.5 0 015 0V6" fill="none" stroke="#fff" stroke-width="1.4"/></svg></div>
</header>

<nav class="main-nav">
  <ul>
    <li style="left:148px">HOME</li>
    <li style="left:228px">ABOUT US</li>
    <li style="left:339px">SERVICES</li>
    <li style="left:449px">PRODUCTS</li>
    <li style="left:566px">PROJECTS</li>
    <li style="left:681px">OUR CLIENTS</li>
    <li style="left:817px">OUR PARTNERS</li>
    <li style="left:968px">CONTACTS</li>
  </ul>
</nav>

<section class="hero">
  <div class="hero-photo" role="img" aria-label="Oil refinery with chimneys and towers at sunset"></div>
  <h1 class="hero-title">Kovadrel Limited</h1>
  <p class="hero-sub">We are engineering consultants and contractors</p>
  <div class="btn btn-framed" style="left:518px;top:313px;width:160px;height:44px">Learn More</div>
  <svg class="hero-curve" viewBox="0 0 1200 80" preserveAspectRatio="none">
    <path d="M0 0 C300 30 700 55 1200 40 L1200 80 L0 80 Z" fill="#ef8a3c"/>
    <path d="M0 60 C300 40 700 30 1200 44 L1200 80 L0 80 Z" fill="#fff"/>
  </svg>
</section>

<section class="about">
  <div class="about-photo-ring"></div>
  <div class="about-photo" role="img" aria-label="Engineer in a hard hat inspecting refinery pipework"></div>
  <div class="about-copy">
    <h2>Who We Are</h2>
    <div class="about-rule"></div>
    <p>Kovadrel undertakes Design, Supply, Installation and Commissioning of LPG and Petroleum systems including LPG Reticulated Systems (piped gas). We also do LPG tank revalidation and recertification.</p>
    <p>Our clients include: Oil companies (both multinationals and local), government agencies, manufacturing companies, agricultural institutions, and the building services industry.</p>
  </div>
  <div class="btn btn-framed" style="left:598px;top:1254px;width:136px;height:40px;font-size:12px">About Us</div>
</section>

<section class="services">
  <h2 class="heading abs" style="left:0;top:80px;width:1200px;font-size:45px">Our Services</h2>
  <div class="heading-rule" style="top:146px;left:548px;width:104px"></div>
  <div class="service-card" style="left:66px;width:202px"><div class="service-icon" role="img" aria-label="EPC icon"></div><div class="service-name">EPC</div><div class="service-link">Read More</div></div>
  <div class="service-card" style="left:280px;width:198px"><div class="service-icon" role="img" aria-label="Oil pump icon"></div><div class="service-name">LPG and<br>Petroleum</div><div class="service-link">Read More</div></div>
  <div class="service-card" style="left:490px;width:222px"><div class="service-icon" role="img" aria-label="Engineer with gear icon"></div><div class="service-name">Engineering Consulting/<br>Project Management</div><div class="service-link">Read More</div></div>
  <div class="service-card" style="left:724px;width:198px"><div class="service-icon" role="img" aria-label="Testing gauge icon"></div><div class="service-name">Non Destructive<br>Testing</div><div class="service-link">Read More</div></div>
  <div class="service-card" style="left:934px;width:198px"><div class="service-icon" role="img" aria-label="Training presenter icon"></div><div class="service-name">Training</div><div class="service-link">Read More</div></div>
</section>

<section class="products">
  <h2 class="heading abs" style="left:0;top:89px;width:1200px;font-size:45px;color:#fff">Products</h2>
  <div class="heading-rule" style="top:155px;left:548px;width:104px"></div>
  <div class="product-card" style="left:124px"><div class="product-photo" role="img" aria-label="LPG storage tanks at a plant" style="background:linear-gradient(180deg,#8aa2c8 0%,#c7b0c4 45%,#e8e8ee 100%)"></div><div class="product-label">LPG</div></div>
  <div class="product-card" style="left:369px"><div class="product-photo" role="img" aria-label="Offshore oil platform at sunset" style="background:linear-gradient(180deg,#6d86a8 0%,#c8a88a 55%,#3d4a5e 100%)"></div><div class="product-label">PETROLEUM</div></div>
  <div class="product-card active" style="left:614px"><div class="product-photo" role="img" aria-label="Technician at an automation control panel" style="background:linear-gradient(180deg,#3c4e64 0%,#2b3b4f 50%,#c68a4a 100%)"></div><div class="product-label">AUTOMATION</div></div>
  <div class="product-card" style="left:860px"><div class="product-photo" role="img" aria-label="Firefighters tackling a fire" style="background:linear-gradient(135deg,#6e8aa5 0%,#b06a55 55%,#e98c3c 100%)"></div><div class="product-label">FIREFIGHTING</div></div>
</section>

<section class="projects">
  <h2 class="heading abs" style="left:0;top:2788px;width:1200px;font-size:45px">Projects</h2>
  <div class="heading-rule" style="top:2849px;left:548px;width:104px"></div>
  <article class="project-card" style="left:130px"><div class="project-photo" role="img" aria-label="Pipelines at sunset" style="background:linear-gradient(180deg,#d98a4a 0%,#f2b46a 40%,#6b3a22 100%)"></div><div class="project-body"><div class="project-title">Piped Gas – LPG<br>Reticulation</div><p class="project-text">Lorem ipsum dolor sit amet, conse ctetur adipiscing elit, sed do eiusmod tempor incididunt ut laboreetdolo.</p><div class="project-link">Read More</div></div></article>
  <article class="project-card" style="left:454px"><div class="project-photo" role="img" aria-label="Petroleum storage terminal at dusk" style="background:linear-gradient(180deg,#3c4a5c 0%,#8a6650 50%,#2f2a26 100%)"></div><div class="project-body"><div class="project-title">Petroleum and LPG<br>Terminals/ Depots</div><p class="project-text">Lorem ipsum dolor sit amet, conse ctetur adipiscing elit, sed do eiusmod tempor incididunt ut laboreetdolo.</p><div class="project-link">Read More</div></div></article>
  <article class="project-card" style="left:779px"><div class="project-photo" role="img" aria-label="Fuel tanker at a petrol station" style="background:linear-gradient(180deg,#7d92ad 0%,#d9d2c2 50%,#7a7a78 100%)"></div><div class="project-body"><div class="project-title">Petrol Stations</div><p class="project-text">Lorem ipsum dolor sit amet, conse ctetur adipiscing elit, sed do eiusmod tempor incididunt ut laboreetdolo.</p><div class="project-link">Read More</div></div></article>
</section>

<section class="clients">
  <svg class="clients-bg" viewBox="0 0 1200 560" preserveAspectRatio="none"><path d="M0 0H1200V560L0 505Z" fill="#efeeef"/></svg>
  <h2 class="heading abs" style="left:0;top:3505px;width:1200px;font-size:45px">Our Clients</h2>
  <div class="heading-rule" style="top:3566px;left:548px;width:104px"></div>
  <p class="quote">Lorem ipsum dolor sit amet, consectetur adipiscing elit, sed do eiusmod tempor incididunt ut labore et dolore magna aliqua. Quis ipsum suspendisse ultrices gravida. Risus commodo viverra maecenas accumsan lacus vel facilisis.</p>
  <div class="client-avatar" role="img" aria-label="Client portrait"></div>
  <div class="client-name">LIAM ODUYA</div>
  <div class="client-role">Lorem Ipsum</div>
</section>

<section class="partners">
  <h2 class="heading abs" style="left:0;top:4025px;width:1200px;font-size:45px">Partners</h2>
  <div class="heading-rule" style="top:4086px;left:548px;width:104px"></div>
  <div class="partner-badge" style="left:146px"></div>
  <div class="partner-badge" style="left:336px"></div>
  <div class="partner-badge" style="left:524px"></div>
  <div class="partner-badge" style="left:744px"></div>
  <div class="partner-badge" style="left:946px"></div>
</section>

<section class="quote-section">
  <h2 class="heading abs" style="left:0;top:63px;width:1200px;font-size:38px;color:#fde5d0">Get A Quote</h2>
</section>
<div class="field" style="left:334px;top:4483px;width:260px;height:42px">Name :</div>
<div class="field" style="left:600px;top:4483px;width:287px;height:42px">Phone :</div>
<div class="field" style="left:334px;top:4534px;width:260px;height:42px">Email :</div>
<div class="field" style="left:600px;top:4534px;width:287px;height:42px">Subject:</div>
<div class="field" style="left:334px;top:4585px;width:553px;height:108px">Message :</div>
<div class="submit">Submit</div>

<footer class="site-footer">
  <div class="footer-skyline" role="img" aria-label="Faint industrial skyline"></div>
</footer>
<div class="brand" style="top:4906px;left:156px">
  <div class="brand-dot" style="width:84px;height:84px"></div>
  <div class="brand-name" style="font-size:25px;line-height:33px">Kovadrel<br>Limited</div>
</div>
<p class="abs" style="left:150px;top:4996px;width:290px;font-size:13px;line-height:22px;color:#444">Kovadrel’ core business is engineering works (Oil and Gas Engineering).</p>
<div class="social" style="left:152px"></div>
<div class="social" style="left:186px"></div>
<div class="social" style="left:220px"></div>

<div class="footer-divider" style="left:473px"></div>
<div class="footer-divider" style="left:676px"></div>

<div class="footer-heading" style="left:522px">Menu</div>
<div class="footer-rule" style="left:522px"></div>
<ul class="footer-menu">
  <li>Home</li><li>About us</li><li>Services</li><li>Products</li><li>Our Projects</li><li>Our Clients</li><li>Partners</li>
</ul>

<div class="footer-heading" style="left:738px">Contact Us</div>
<div class="footer-rule" style="left:738px"></div>
<div class="contact-row" style="top:4940px">
  <div class="chip-icon"><svg width="16" height="16" viewBox="0 0 24 24"><path fill="#fff" d="M6.6 10.8a15.1 15.1 0 006.6 6.6l2.2-2.2c.3-.3.7-.4 1-.2 1.1.4 2.3.6 3.6.6.6 0 1 .4 1 1V20c0 .6-.4 1-1 1A17 17 0 013 4c0-.6.4-1 1-1h3.5c.6 0 1 .4 1 1 0 1.3.2 2.5.6 3.6.1.3 0 .7-.2 1z"/></svg></div>
  <span>Harlow Court, Next to Meridian<br>Mall, Kilima, Suite 14, Baraka Road<br>P.O. Box 40210-00100 Kisumu</span>
</div>
<div class="contact-row" style="top:5018px">
  <div class="chip-icon"><svg width="16" height="16" viewBox="0 0 24 24"><path fill="#fff" d="M6.6 10.8a15.1 15.1 0 006.6 6.6l2.2-2.2c.3-.3.7-.4 1-.2 1.1.4 2.3.6 3.6.6.6 0 1 .4 1 1V20c0 .6-.4 1-1 1A17 17 0 013 4c0-.6.4-1 1-1h3.5c.6 0 1 .4 1 1 0 1.3.2 2.5.6 3.6.1.3 0 .7-.2 1z"/></svg></div>
  <span style="line-height:36px">Cell: +254 700 555 038, +254 700 555 014</span>
</div>
<div class="contact-row" style="top:5064px">
  <div class="chip-icon"><svg width="16" height="12" viewBox="0 0 16 12"><rect x="0.5" y="0.5" width="15" height="11" rx="1.5" fill="none" stroke="#fff"/><path d="M1 1l7 6 7-6" fill="none" stroke="#fff"/></svg></div>
  <span style="line-height:36px">info@kovadrel.co.ke</span>
</div>

<p class="copyright">Copyrights © 2023 Kovadrel Limited. All rights Reserved</p>

</body>
</html>
```